Harborline Renewal Business Card Design

Professional and clean design. The design colors should flow with the logo. Two-sided card with the website on the back which is:

www.HarborlineRenewal.example.

"Specializing in Water Damage Restoration"

On the front I need the name, email, phone, and logo.

Name: Darnell Quisby
Email: Darnell@HarborlineRenewal.example
Phone: 555-318-2046 for now

I only have the Preview and Thumbnail right now but should have the source files uploaded within a day or two.

Target Market(s)

Flood victims, home owners with water damage from busted pipes etc...

Industry/Entity Type

Business

Contact Information for Business Card

Name: Darnell Quisby

Font styles to use
Serif
Sans Serif

Requirements
Must have
• Business Card Details Info

```html
<!DOCTYPE html>
<html lang="en">
<head>
<meta charset="utf-8">
<title>Harborline Renewal Business Card</title>
<link href="https://fonts.googleapis.com/css2?family=Tinos:wght@400;700&display=swap" rel="stylesheet">
<style>
  :root {
    --stage: #2b2b2b;
    --sky: #4aaee2;
    --sky-deep: #2f9ad6;
    --sky-light: #6cc2ec;
    --sky-pale: #bfe3f6;
    --paper: #ffffff;
    --ink: #3a3a3a;
  }
  * { margin: 0; padding: 0; box-sizing: border-box; }
  html, body {
    width: 1200px; height: 913px; overflow: hidden;
    background: var(--stage);
    font-family: "Tinos", "Times New Roman", serif;
  }
  .stage {
    position: relative; width: 1200px; height: 913px;
    display: flex; align-items: center; justify-content: center; gap: 40px;
  }
  .card {
    position: relative; width: 540px; height: 309px; overflow: hidden;
    box-shadow: 0 10px 30px rgba(0,0,0,.45);
  }
  /* back side */
  .card--back {
    background: linear-gradient(135deg, var(--sky-light) 0%, var(--sky) 50%, var(--sky-deep) 100%);
    color: var(--paper);
  }
  .back-copy { position: absolute; left: 34px; bottom: 50px; }
  .back-site { font-size: 15px; letter-spacing: .3px; margin-bottom: 8px; }
  .back-tagline { font-size: 21px; font-weight: 700; letter-spacing: .2px; }
  .brand {
    display: flex; align-items: center; gap: 12px;
    font-weight: 400; text-transform: uppercase; letter-spacing: 1.5px;
  }
  .brand-dot { width: 38px; height: 38px; border-radius: 50%; flex: none; }
  .brand-name { font-size: 25px; line-height: 1; }
  .card--back .brand { position: absolute; right: 34px; top: 106px; }
  .card--back .brand-dot { background: var(--paper); }
  .card--back .brand-name { color: var(--paper); }
  /* front side */
  .card--front { background: var(--paper); }
  .front-corner {
    position: absolute; left: -70px; bottom: -150px;
    width: 290px; height: 290px; border-radius: 50%;
    background: var(--sky-pale);
  }
  .card--front .brand { position: absolute; right: 30px; top: 40px; }
  .card--front .brand-dot { background: var(--sky-deep); }
  .card--front .brand-name { color: var(--sky-deep); }
  .contact { position: absolute; right: 30px; top: 128px; text-align: right; }
  .contact-name {
    color: var(--sky-deep); font-weight: 700; font-size: 19px;
    text-transform: uppercase; letter-spacing: .5px; margin-bottom: 16px;
  }
  .contact-line {
    display: flex; align-items: center; justify-content: flex-end; gap: 8px;
    color: var(--ink); font-size: 15px; margin-bottom: 8px;
  }
  .contact-line svg { width: 14px; height: 14px; fill: var(--sky); flex: none; }
</style>
</head>
<body>
<main class="stage">
  <section class="card card--back" aria-label="Card back">
    <div class="brand">
      <span class="brand-dot"></span>
      <span class="brand-name">Harborline Renewal</span>
    </div>
    <div class="back-copy">
      <p class="back-site">www.HarborlineRenewal.example</p>
      <p class="back-tagline">Specializing in Water Damage Restoration</p>
    </div>
  </section>

  <section class="card card--front" aria-label="Card front">
    <div class="front-corner"></div>
    <div class="brand">
      <span class="brand-dot"></span>
      <span class="brand-name">Harborline Renewal</span>
    </div>
    <div class="contact">
      <p class="contact-name">Darnell Quisby</p>
      <p class="contact-line">555-318-2046
        <svg viewBox="0 0 24 24" aria-hidden="true"><path d="M6.6 10.8a15.1 15.1 0 0 0 6.6 6.6l2.2-2.2a1 1 0 0 1 1-.25 11.4 11.4 0 0 0 3.6.57 1 1 0 0 1 1 1V20a1 1 0 0 1-1 1A17 17 0 0 1 3 4a1 1 0 0 1 1-1h3.5a1 1 0 0 1 1 1c0 1.25.2 2.45.57 3.6a1 1 0 0 1-.25 1z"/></svg>
      </p>
      <p class="contact-line">Darnell@HarborlineRenewal.example
        <svg viewBox="0 0 24 24" aria-hidden="true"><path d="M3 5h18a1 1 0 0 1 1 1v12a1 1 0 0 1-1 1H3a1 1 0 0 1-1-1V6a1 1 0 0 1 1-1zm9 7.5L20 7H4z"/></svg>
      </p>
    </div>
  </section>
</main>
</body>
</html>
```